Business Card Design

Company is a Commercial Building Company specialising in New Construction and existing refurbishments

Industry/Entity Type

Business

Contact Information for Business Card

Liam Porter
Construction Manager
E Liam@marshbuilding.com.au
M 0400 213 594
Mail 14 Tarrant Rise Harlow Bay WA 6190

```html
<!DOCTYPE html>
<html lang="en">
<head>
<meta charset="utf-8">
<title>Marsh Building &amp; Construction — Business Cards</title>
<link href="https://fonts.googleapis.com/css2?family=Arimo:wght@400;700&display=swap" rel="stylesheet">
<style>
  :root {
    --backdrop: #e9e6e1;
    --card: #ffffff;
    --orange: #f28a1c;
    --blue: #05b4d3;
    --ink: #2b2f3a;
    --text: #2f2f2f;
  }
  * { margin: 0; padding: 0; box-sizing: border-box; }
  html, body {
    width: 1200px; height: 858px; overflow: hidden;
    background: var(--backdrop);
    font-family: "Arimo", Arial, sans-serif;
  }
  .sheet {
    width: 1200px; height: 858px;
    display: flex; align-items: center; justify-content: center; gap: 40px;
  }
  .card {
    position: relative;
    width: 540px; height: 309px;
    background: var(--card);
    box-shadow: 0 6px 18px rgba(0,0,0,.18);
    overflow: hidden;
  }
  .band { position: absolute; width: 22px; }
  .band--orange { background: var(--orange); }
  .band--blue { background: var(--blue); }

  .card--front .band--orange { left: 0; top: 22px; bottom: 0; border-top-right-radius: 14px; }
  .card--front .band--blue { right: 0; top: 0; bottom: 26px; border-bottom-left-radius: 14px; }
  .card--back .band--blue { left: 0; top: 0; bottom: 30px; border-bottom-right-radius: 14px; }
  .card--back .band--orange { right: 0; top: 0; height: 70px; border-bottom-left-radius: 14px; }

  .brand { display: flex; align-items: center; gap: 10px; color: var(--ink); }
  .brand__mark { width: 30px; height: 30px; border: 4px solid var(--blue); flex: none; }
  .brand__name { font-weight: 700; text-transform: uppercase; line-height: 1.1; }

  .card--front .brand { position: absolute; left: 62px; top: 60px; }
  .card--front .brand__name { font-size: 15px; }

  .person { position: absolute; left: 110px; top: 122px; color: var(--text); }
  .person__name { font-size: 21px; font-weight: 400; }
  .person__role { font-size: 15px; margin-top: 2px; }

  .contact { position: absolute; left: 170px; top: 200px; color: var(--text); font-size: 15px; line-height: 1.45; list-style: none; }

  .card--back .brand { position: absolute; left: 50%; top: 50%; transform: translate(-50%, -50%); gap: 14px; }
  .card--back .brand__mark { width: 42px; height: 42px; border-width: 5px; }
  .card--back .brand__name { font-size: 20px; }
</style>
</head>
<body>
<main class="sheet">
  <section class="card card--front" aria-label="Business card front">
    <div class="band band--orange"></div>
    <div class="band band--blue"></div>
    <div class="brand">
      <span class="brand__mark"></span>
      <span class="brand__name">Marsh Building<br>&amp; Construction</span>
    </div>
    <div class="person">
      <p class="person__name">Liam Porter</p>
      <p class="person__role">Construction Manager</p>
    </div>
    <ul class="contact">
      <li>0400 213 594</li>
      <li>Liam@marshbuilding.com.au</li>
      <li>14 Tarrant Rise Harlow Bay WA 6190</li>
    </ul>
  </section>

  <section class="card card--back" aria-label="Business card back">
    <div class="band band--blue"></div>
    <div class="band band--orange"></div>
    <div class="brand">
      <span class="brand__mark"></span>
      <span class="brand__name">Marsh Building<br>&amp; Construction</span>
    </div>
  </section>
</main>
</body>
</html>
```